Update our OBGYN business card look and info

We are an OBGYN office. Our logo is nice but would like to "woman" part of the logo to be a darker color, to contrast with the flower that surrounds it. Maybe make our practice name Bloom Harbor Health more feminine. Our practice caters to women only. All providers and staff are female.

Target Market(s)

Females 16-65.

Industry/Entity Type

Business

Contact Information for Business Card

See attached upload. The ONLY CHANGE to the information is DELETE the name Paula Renwick, Midwife and REPLACE with Dora Fintelli, Midwife

Logo Text

Bloom Harbor Health Obstetrics & Gynecology

Font styles to use
Serif
Script

Colors
85cae6
0692cd
33a6d7
85abd2
f59195
eea4c8
cadf82
fac994
d3a5cc

```html
<!DOCTYPE html>
<html lang="en">
<head>
<meta charset="utf-8">
<title>Bloom Harbor Health – Business Card</title>
<link rel="stylesheet" href="https://fonts.googleapis.com/css2?family=Marcellus&family=Questrial&family=Open+Sans:wght@400;600;700&display=swap">
<style>
  :root {
    --page-bg: #e9e6e3;
    --card-white: #ffffff;
    --card-black: #141414;
    --brand-blue: #33a6d7;
    --brand-green: #cadf82;
    --name-green: #bfd870;
    --text-white: #ffffff;
  }
  * { margin: 0; padding: 0; box-sizing: border-box; }
  html, body { width: 1200px; height: 900px; overflow: hidden; }
  body {
    position: relative;
    background: var(--page-bg);
    font-family: "Open Sans", Arial, sans-serif;
  }
  .card {
    position: absolute;
    overflow: hidden;
    box-shadow: 0 6px 18px rgba(0,0,0,0.18);
  }
  .card-front {
    left: 78px; top: 34px;
    width: 588px; height: 364px;
    background: var(--card-white);
  }
  .card-back {
    left: 388px; top: 505px;
    width: 566px; height: 352px;
    background: var(--card-black);
  }
  .front-bands { position: absolute; left: 0; top: 0; }

  .brand {
    position: absolute;
    display: flex;
    align-items: center;
    gap: 24px;
  }
  .brand-dot {
    width: 66px; height: 66px;
    border-radius: 50%;
    background: var(--brand-blue);
    flex: none;
  }
  .brand-text { display: flex; flex-direction: column; }
  .brand-name {
    font-family: "Marcellus", "Times New Roman", serif;
    font-weight: 400;
    font-size: 17px;
    line-height: 24px;
    text-transform: uppercase;
    color: var(--name-green);
    white-space: nowrap;
  }
  .brand-tagline {
    font-family: "Questrial", "Century Gothic", sans-serif;
    font-size: 18.5px;
    line-height: 26px;
    color: var(--brand-blue);
    white-space: nowrap;
  }
  .card-front .brand { left: 118px; top: 48px; }
  .card-back .brand { left: 109px; top: 145px; }

  .contact {
    position: absolute;
    left: 33px; top: 231px;
    list-style: none;
    color: var(--text-white);
    font-size: 15.5px;
    line-height: 22px;
  }
  .contact li { display: flex; align-items: center; gap: 9px; }
  .contact .icon { width: 14px; height: 14px; flex: none; }

  .providers {
    position: absolute;
    right: 37px; top: 212px;
    list-style: none;
    text-align: right;
    color: var(--text-white);
    font-weight: 600;
    font-size: 15.5px;
    line-height: 26.5px;
    text-transform: uppercase;
  }
</style>
</head>
<body>

<section class="card card-front" aria-label="Business card front">
  <svg class="front-bands" width="588" height="364" viewBox="0 0 588 364" aria-hidden="true">
    <polygon points="0,168 392,168 372,202 0,202" fill="var(--brand-green)"/>
    <polygon points="405,158 588,158 588,364 0,364 0,204 375,204" fill="var(--brand-blue)"/>
  </svg>

  <div class="brand">
    <span class="brand-dot"></span>
    <span class="brand-text">
      <span class="brand-name">Bloom Harbor Health</span>
      <span class="brand-tagline">Obstetrics &amp; Gynecology</span>
    </span>
  </div>

  <ul class="contact">
    <li>
      <svg class="icon" viewBox="0 0 16 16" aria-hidden="true"><path fill="#fff" d="M3.6 1.2l2.3 2.9-1.4 1.8c.9 1.9 2.7 3.7 4.6 4.6l1.8-1.4 2.9 2.3-1.3 2.3C7.5 13.6 2.4 8.5 1.3 3.6z"/></svg>
      <span>555-210-4471</span>
    </li>
    <li>
      <svg class="icon" viewBox="0 0 16 16" aria-hidden="true"><rect x="2" y="5" width="12" height="9" rx="1" fill="#fff"/><rect x="4.5" y="1.5" width="7" height="4" fill="#fff"/><rect x="5" y="8" width="6" height="1.2" fill="var(--brand-blue)"/><rect x="5" y="10.4" width="6" height="1.2" fill="var(--brand-blue)"/></svg>
      <span>555-210-4472</span>
    </li>
    <li>
      <svg class="icon" viewBox="0 0 16 16" aria-hidden="true"><circle cx="8" cy="8" r="7" fill="#fff"/><path d="M1.5 8h13M8 1c-3 3.5-3 10.5 0 14M8 1c3 3.5 3 10.5 0 14" stroke="var(--brand-blue)" stroke-width="1.1" fill="none"/></svg>
      <span>www.bloomharborhealth.com</span>
    </li>
    <li>240 Linden Ave. Ste 3B</li>
    <li>Fairview,GA 30000-1234</li>
  </ul>

  <ul class="providers">
    <li>Marian Oakes,MD</li>
    <li>Lena Hartwell,MD</li>
    <li>Lena Hartwell,MD</li>
    <li>Dora Fintelli, Midwife</li>
    <li>Celia Brandt,Midwife</li>
  </ul>
</section>

<section class="card card-back" aria-label="Business card back">
  <div class="brand">
    <span class="brand-dot"></span>
    <span class="brand-text">
      <span class="brand-name">Bloom Harbor Health</span>
      <span class="brand-tagline">Obstetrics &amp; Gynecology</span>
    </span>
  </div>
</section>

</body>
</html>
```